Flowmark Engineering Business Card

our company has just rebranded and taken on a new logo design. We now need to update our business cards with the new logo. This is also an opportunity to reformat and modernize our look. We are an engineering company so the look needs to be formal and professional yet it should look modern. Have a look at our current card and the new card should have the same information.

Target Market(s)

Engineering firms, government, mining companies

Industry/Entity Type

Mechanical Engineering

Contact Information for Business Card

see example attached

Requirements
Must have
• look professional and modern
Should not have
• should not include the office locations 'Brisbane, Sydney and Kuala Lumpur'
• you will find this on the example but it should not be included in these versions. please remove from your submissions and resubmit

```html
<!DOCTYPE html>
<html lang="en">
<head>
<meta charset="utf-8">
<title>Flowmark Engineering – Business Card</title>
<link rel="stylesheet" href="https://fonts.googleapis.com/css2?family=Montserrat:wght@400;500;700&display=swap">
<style>
  :root {
    --page-bg: #e6e6e6;
    --card-white: #ffffff;
    --brand-navy: #3a45a8;
    --blue-light: #0aa6e8;
    --blue-deep: #2f5fb8;
    --band-grey: #6f7175;
    --text-light: #ffffff;
  }
  * { margin: 0; padding: 0; box-sizing: border-box; }
  html, body {
    width: 1200px; height: 900px; overflow: hidden;
    background: var(--page-bg);
    font-family: "Montserrat", sans-serif;
  }
  .business-card {
    position: absolute; left: 180px; top: 210px;
    width: 840px; height: 480px;
    background: var(--card-white);
    box-shadow: 0 18px 40px rgba(0,0,0,0.18);
    overflow: hidden;
  }
  .card-shapes { position: absolute; inset: 0; }
  .brand-block {
    position: absolute; left: 40px; top: 190px;
    display: flex; align-items: center; gap: 18px;
  }
  .brand-dot {
    width: 58px; height: 58px; border-radius: 50%;
    border: 5px solid var(--brand-navy);
  }
  .brand-name {
    color: var(--brand-navy); font-weight: 700;
    font-size: 30px; letter-spacing: 2px; line-height: 1.15;
    text-transform: uppercase;
  }
  .contact-block {
    position: absolute; right: 44px; top: 44px;
    text-align: right; color: var(--text-light);
  }
  .person-name { font-size: 26px; font-weight: 500; letter-spacing: 2px; text-transform: uppercase; }
  .person-role { font-size: 16px; letter-spacing: 1.5px; text-transform: uppercase; margin-top: 2px; }
  .address { font-size: 17px; line-height: 1.35; margin-top: 46px; letter-spacing: 0.5px; }
  .contact-list { list-style: none; margin-top: 40px; font-size: 16px; line-height: 1.95; letter-spacing: 0.5px; }
  .contact-list li { display: flex; justify-content: flex-end; align-items: center; gap: 10px; }
  .contact-icon { width: 16px; height: 16px; fill: var(--text-light); }
</style>
</head>
<body>
  <div class="business-card">
    <svg class="card-shapes" width="840" height="480" viewBox="0 0 840 480">
      <defs>
        <radialGradient id="panelGradient" cx="0.45" cy="0.6" r="0.75">
          <stop offset="0" stop-color="var(--blue-light)"/>
          <stop offset="1" stop-color="var(--blue-deep)"/>
        </radialGradient>
      </defs>
      <path class="curve-band" d="M300 0 C400 110 425 320 350 480 L372 480 C450 330 428 120 340 0 Z" fill="var(--band-grey)"/>
      <path class="contact-panel" d="M340 0 C428 120 450 330 372 480 L840 480 L840 0 Z" fill="url(#panelGradient)"/>
    </svg>

    <div class="brand-block">
      <span class="brand-dot"></span>
      <div class="brand-name">Flowmark<br>Engineering</div>
    </div>

    <div class="contact-block">
      <div class="person-name">Daniel Reeve</div>
      <div class="person-role">Financial Advisor</div>
      <div class="address">204: 12th floor Harbour<br>Canal Road NKD</div>
      <ul class="contact-list">
        <li>021 555 0148
          <svg class="contact-icon" viewBox="0 0 16 16"><path d="M3 1l3 3-2 2c1 2 3 4 5 5l2-2 3 3-2 3C7 15 1 9 1 3z"/></svg></li>
        <li>021 555 0148
          <svg class="contact-icon" viewBox="0 0 16 16"><path d="M4 0h8a1 1 0 011 1v14a1 1 0 01-1 1H4a1 1 0 01-1-1V1a1 1 0 011-1zm1 2v10h6V2z"/></svg></li>
        <li>021 555 0148
          <svg class="contact-icon" viewBox="0 0 16 16"><path d="M4 1h6v4H4zM2 6h12v8H2zm2 2v2h4V8z"/></svg></li>
        <li>info@flowmarkeng.com
          <svg class="contact-icon" viewBox="0 0 16 16"><path d="M1 3h14v10H1zm1 1l6 5 6-5z"/></svg></li>
        <li>www.flowmarkeng.com
          <svg class="contact-icon" viewBox="0 0 16 16"><path d="M8 1a7 7 0 100 14A7 7 0 008 1zm0 1.5c1 1 1.6 2.6 1.7 4.5H6.3C6.4 5.1 7 3.5 8 2.5zM2.6 7h2.2c.1-1.6.5-3 1.2-4A5.5 5.5 0 002.6 7zm0 2A5.5 5.5 0 006 13c-.7-1-1.1-2.4-1.2-4zm3.7 0c.1 1.9.7 3.5 1.7 4.5 1-1 1.6-2.6 1.7-4.5zm4.9 0c-.1 1.6-.5 3-1.2 4a5.5 5.5 0 003.4-4zm0-2h2.2A5.5 5.5 0 0010 3c.7 1 1.1 2.4 1.2 4z"/></svg></li>
      </ul>
    </div>
  </div>
</body>
</html>
```